Torvane Email Signature Banners – Fabrication Capability Series

www.Torvane.com.au is an Australian engineering and fabrication company specialising in fabrication and welding of :
steel piping spools,
skids and frames,
small volume process steel tanks
and general steel fabrication
We require four distinct banner designs for use in Microsoft Lintaro email signatures. Each banner will highlight a specific capability while maintaining a consistent brand identity.
Deliverables
Four banners total:
Piping Spools Fabrication – focus on precision welding and stainless steel pipework
Skid & Frames Fabrication – highlight skid systems and structural frames
Small Steel Tanks Fabrication – show fabricated tanks and workshop craftsmanship
General Fabrication Solutions – broad steel fabrication theme for company-wide use
Dimensions: 600–700 px wide × 100 px high
Format: PNG (preferred), small file size prefered
Resolution: 72 dpi
Background: non-transparent, industrial or workshop setting
Text examples:
1. Piping Spools Fabrication
Option A: “Expert Fabrication Solutions for Process Piping”
Option B: “Precision Welding for Complex Systems”
Option C: “Delivering Quality in Every Spool”
Option D: “Engineered for Flow, Built for Strength”
2. Skid & Frames Fabrication
Option A: “Custom Engineered Modular Systems”
Option B: “Built Strong. Designed Smart.”
Option C: “Reliable Frames for Industrial Performance”
Option D: “Modular Fabrication for Seamless Integration”
3. Small Steel Tanks Fabrication
Option A: “Precision Built for Your Needs”
Option B: “Compact Strength. Proven Durability.”
Option C: “Fabricated for Performance and Longevity”
Option D: “Small Tanks. Big Reliability.”
4. General Fabrication Solutions
Option A: “Quality Craftsmanship, Proven Results”
Option B: “Your Partner in Precision Fabrication”
Option C: “Engineering Excellence in Every Weld”
Option D: “Australian Fabrication. Global Standards.”
Style Direction
Clean, professional, and engineering‑focused
Use Torvane brand colours
Blend photo realism with vector clarity (no heavy gradients)
Include subtle industrial textures or workshop imagery
Typography: bold sans‑serif, legible at small scale
Usage Context
These banners will appear at the bottom of staff email signatures via Lintaro Email Signature Tool for Microsoft 365, so clarity and fast loading are essential. No Logo is required in the banners.
Reference
Existing Torvane signature is attached. Colour palette to match the signature style and logo.
Target Market(s)
Engineering and construction companies,
Industry/Entity Type
Engineering fabrication design
Look and feel

```html
<!DOCTYPE html>
<html lang="en">
<head>
<meta charset="utf-8">
<title>Torvane Fabrication Banners</title>
<link href="https://fonts.googleapis.com/css2?family=Montserrat:wght@500;600;800&display=swap" rel="stylesheet">
<style>
  :root {
    --canvas-grey: #6d6d6d;
    --panel-white: #f7f8f9;
    --brand-blue: #2a9fdb;
    --steel-grey: #7b8087;
    --ink: #2b2f33;
    --rule: #c9cdd1;
  }
  html, body {
    margin: 0;
    padding: 0;
    width: 1200px;
    height: 427px;
    overflow: hidden;
    background: var(--canvas-grey);
    font-family: "Montserrat", Arial, sans-serif;
  }
  .canvas {
    position: relative;
    width: 1200px;
    height: 427px;
  }
  .banner {
    position: absolute;
    left: 16px;
    width: 1168px;
    height: 190px;
    background: var(--panel-white);
    overflow: hidden;
  }
  .banner--spools { top: 16px; }
  .banner--tanks { top: 221px; }
  .banner svg.frame {
    position: absolute;
    inset: 0;
    width: 1168px;
    height: 190px;
  }
  .copy {
    position: absolute;
    top: 0;
    height: 190px;
    display: flex;
    flex-direction: column;
    justify-content: center;
    align-items: center;
    text-align: center;
  }
  .headline {
    margin: 0;
    color: var(--brand-blue);
    font-weight: 800;
    font-size: 37px;
    line-height: 1.05;
    letter-spacing: 0.5px;
  }
  .subhead {
    margin: 0;
    color: var(--steel-grey);
    font-weight: 600;
    font-size: 33px;
    line-height: 1.1;
    letter-spacing: 1px;
  }
  .divider {
    width: 230px;
    height: 2px;
    background: var(--rule);
    margin: 14px 0 12px;
  }
  .tagline {
    margin: 0;
    color: var(--ink);
    font-weight: 500;
    font-size: 22px;
    line-height: 1.3;
  }
  .copy--spools { left: 370px; width: 465px; }
  .copy--tanks { left: 0; width: 450px; }
  .copy--promise { left: 740px; width: 428px; }
</style>
</head>
<body>
<main class="canvas">

  <section class="banner banner--spools">
    <svg class="frame" viewBox="0 0 1168 190" aria-hidden="false">
      <defs>
        <linearGradient id="pipeCrew" x1="0" y1="0" x2="1" y2="1">
          <stop offset="0" stop-color="#2e3a48"/>
          <stop offset="0.5" stop-color="#4d5d6e"/>
          <stop offset="1" stop-color="#8a6a52"/>
        </linearGradient>
        <linearGradient id="pipeWelder" x1="0" y1="0" x2="1" y2="1">
          <stop offset="0" stop-color="#9fb2c2"/>
          <stop offset="0.5" stop-color="#6f8393"/>
          <stop offset="1" stop-color="#3f4b56"/>
        </linearGradient>
      </defs>
      <rect x="0" y="0" width="380" height="190" fill="url(#pipeCrew)" role="img" aria-label="Photo of workers in safety gear beside large coated steel pipe spools"/>
      <rect x="825" y="0" width="343" height="190" fill="url(#pipeWelder)" role="img" aria-label="Photo of a welder joining stainless steel pipework in a workshop"/>
      <polygon points="370,0 835,0 865,95 835,190 370,190 340,95" fill="var(--panel-white)" stroke="var(--brand-blue)" stroke-width="9" stroke-linejoin="miter"/>
    </svg>
    <div class="copy copy--spools">
      <h2 class="headline">PIPING SPOOLS</h2>
      <p class="subhead">FABRICATION</p>
      <div class="divider"></div>
      <p class="tagline">Expert Fabrication Solutions for<br>Process Piping</p>
    </div>
  </section>

  <section class="banner banner--tanks">
    <svg class="frame" viewBox="0 0 1168 190">
      <defs>
        <linearGradient id="tankShop" x1="0" y1="0" x2="1" y2="1">
          <stop offset="0" stop-color="#c7ccd0"/>
          <stop offset="0.5" stop-color="#8d9499"/>
          <stop offset="1" stop-color="#4f565c"/>
        </linearGradient>
      </defs>
      <polygon points="470,0 715,0 742,95 715,190 470,190 443,95" fill="url(#tankShop)" stroke="var(--brand-blue)" stroke-width="9" stroke-linejoin="miter" role="img" aria-label="Photo of a technician in cleanroom clothing working beside polished stainless steel tanks"/>
    </svg>
    <div class="copy copy--tanks">
      <h2 class="headline">SMALL STEEL TANKS</h2>
      <p class="subhead">FABRICATION</p>
    </div>
    <div class="copy copy--promise">
      <h2 class="headline">PRECISION BUILT</h2>
      <p class="subhead">FOR YOUR NEEDS</p>
    </div>
  </section>

</main>
</body>
</html>
```